New business card/stationary for a consulting company

I am looking for a clean and very professional looking business card for my consulting company as well as corresponding stationary. I am uploading our logo. I like simple and powerful for the feel. No graphics but I am open on everything else. Below is my contact information but would like the final to be in a version I can add my employees information into and print. Thank you.

Daniel Whitcombe
dan@ferncliffadvisory.com
2870 North 9th Avenue, Summit Floor, Elm Ridge, Illinois 60531
www.ferncliffadvisory.com

Industry/Entity Type

Consulting

Contact Information for Business Card

Daniel Whitcombe
dan@ferncliffadvisory.com
www.ferncliffadvisory.com

Font styles to use
Serif
Sans Serif

Requirements
Must have
• Our logo and the business card details.
Nice to have
• our website www.ferncliffadvisory.com

```html
<!DOCTYPE html>
<html lang="en">
<head>
<meta charset="utf-8">
<title>Ferncliff Advisory — Business Cards</title>
<link href="https://fonts.googleapis.com/css2?family=Montserrat:wght@300;400;700&family=Roboto:wght@400;700&display=swap" rel="stylesheet">
<style>
  :root {
    --navy: #020b82;
    --paper: #f7f7f7;
    --ink-grey: #6b6b6b;
    --ink-dark: #4a4a4a;
    --backdrop: #d9d6d0;
    --white: #ffffff;
  }
  * { margin: 0; padding: 0; box-sizing: border-box; }
  html, body {
    width: 1200px; height: 886px; overflow: hidden;
    background: var(--backdrop);
  }
  .stage { position: relative; width: 1200px; height: 886px; }

  .card { position: absolute; box-shadow: 0 6px 18px rgba(0,0,0,0.25); overflow: hidden; }

  /* Front card */
  .card-front {
    left: 150px; top: 145px; width: 340px; height: 595px;
    background: var(--paper);
  }
  .contact {
    position: absolute; left: 40px; right: 30px; top: 150px;
    font-family: "Roboto", sans-serif; color: var(--ink-grey);
  }
  .contact-name {
    font-family: "Montserrat", sans-serif; font-weight: 700;
    font-variant: small-caps; font-size: 24px; letter-spacing: 1px;
    color: var(--navy); margin-bottom: 4px;
  }
  .contact-email { font-size: 13px; margin-bottom: 18px; }
  .contact-address { font-size: 13px; line-height: 1.45; }
  .contact-web {
    font-size: 13px; font-weight: 700; color: var(--ink-dark);
    text-transform: uppercase; letter-spacing: 0.3px;
  }
  .front-band {
    position: absolute; left: 0; right: 0; bottom: 0; height: 190px;
    background: var(--navy);
    display: flex; align-items: center; justify-content: center;
  }
  .brand-name {
    font-family: "Montserrat", sans-serif; font-weight: 300;
    color: var(--white); text-transform: uppercase; letter-spacing: 3px;
    text-align: center;
  }
  .front-band .brand-name { font-size: 30px; line-height: 1.2; }

  /* Back card */
  .card-back {
    left: 570px; top: 283px; width: 560px; height: 320px;
    background: var(--navy);
    display: flex; flex-direction: column; align-items: center; justify-content: center; gap: 26px;
  }
  .brand-mark { width: 26px; height: 26px; background: var(--white); }
  .card-back .brand-name { font-size: 30px; }
</style>
</head>
<body>
<main class="stage">
  <section class="card card-front" aria-label="Business card front">
    <div class="contact">
      <p class="contact-name">Daniel Whitcombe</p>
      <p class="contact-email">dan@ferncliffadvisory.com</p>
      <p class="contact-address">2870 North 9th Avenue<br>Summit Floor, Elm Ridge, Illinois 60531</p>
      <p class="contact-web">www.ferncliffadvisory.com</p>
    </div>
    <div class="front-band">
      <p class="brand-name">Ferncliff<br>Advisory</p>
    </div>
  </section>

  <section class="card card-back" aria-label="Business card back">
    <span class="brand-mark" aria-hidden="true"></span>
    <p class="brand-name">Ferncliff Advisory</p>
  </section>
</main>
</body>
</html>
```